Professional BIO Template with photo and logo

Hello,
I need a professional Bio template developed via Microsoft WORD ASAP!!!!! I would like to just be able to add the text I need to add. So resize-able text boxes. Potentially able to adjust the font. These are the things I need added it to include.
Head shot (attached)
Text Box for Name
Text Box for phone number
Text box for email
KVT Logo (attached)
Maybe a blue banner at the top or some background boxes that are blue or grey. Here are the pantone colors that our company uses.

CORE COLOR
100c 91m 17y 6k 38r 58g 128b Hex #263A80 Pantone 7687 C

CORE CONTRAST COLOR
36c 29m 28y 0k 168r 168g 170b Hex #669999 Pantone Cool Gray 6C

I also attached some examples of what we have been looking at. Instead of green add the blue...instead of black maybe just be white.

Thank you

```html
<!DOCTYPE html>
<html lang="en">
<head>
<meta charset="UTF-8">
<title>Daniel Rowe – Bio</title>
<link rel="stylesheet" href="https://fonts.googleapis.com/css2?family=Michroma&family=Roboto+Condensed:wght@400;700&display=swap">
<style>
  :root {
    --core-blue: #263a80;
    --deep-violet: #352b72;
    --contrast-grey: #afaaab;
    --text-grey: #7a7a7a;
    --label-grey: #a3a3a3;
    --icon-blue: #2f2f86;
    --white: #ffffff;
  }
  * { margin: 0; padding: 0; box-sizing: border-box; }
  html, body { width: 848px; height: 1200px; overflow: hidden; background: var(--white); }
  .bio-page { position: relative; width: 848px; height: 1200px; overflow: hidden; background: var(--white); }

  .blue-band {
    position: absolute; left: 0; top: 255px; width: 848px; height: 945px;
    background: linear-gradient(160deg, var(--core-blue) 0%, #2d3479 50%, var(--deep-violet) 100%);
  }
  .grey-panel {
    position: absolute; left: 52px; top: 0; width: 325px; height: 261px;
    background: var(--contrast-grey);
  }
  .photo-ring {
    position: absolute; left: 52px; top: 98px; width: 326px; height: 326px;
    border-radius: 50%; background: var(--contrast-grey);
  }
  .headshot {
    position: absolute; left: 65px; top: 111px; width: 300px; height: 300px;
    border-radius: 50%;
    background: radial-gradient(circle at 50% 40%, #8a7060 0%, #5a5a5c 45%, #2e2f36 100%);
  }

  .person-name {
    position: absolute; left: 440px; top: 42px;
    font-family: "Michroma", sans-serif; font-size: 31px; letter-spacing: -0.5px;
    color: var(--core-blue); white-space: nowrap;
  }
  .person-name .first { color: var(--contrast-grey); }

  .contact { position: absolute; left: 441px; }
  .contact.phone { top: 105px; }
  .contact.email { top: 169px; }
  .contact-icon { position: absolute; left: 0; top: 0; width: 41px; height: 41px; }
  .contact-label {
    position: absolute; left: 57px; top: 0; white-space: nowrap;
    font-family: "Roboto Condensed", sans-serif; font-size: 13px; color: var(--label-grey);
  }
  .contact-value {
    position: absolute; left: 57px; top: 14px; white-space: nowrap;
    font-family: "Roboto Condensed", sans-serif; font-weight: 700; font-size: 21px; color: var(--text-grey);
  }

  .brand-name {
    position: absolute; right: 52px; top: 330px;
    font-family: "Roboto Condensed", sans-serif; font-weight: 700; font-size: 44px;
    letter-spacing: 3px; color: var(--white);
  }

  .about-title {
    position: absolute; left: 52px; top: 482px;
    font-family: "Michroma", sans-serif; font-size: 36px; color: var(--white); letter-spacing: 0.5px;
  }
  .about-text {
    position: absolute; left: 52px; top: 561px; width: 744px;
    font-family: "Roboto Condensed", sans-serif; font-size: 15.6px; line-height: 26.3px;
    color: var(--white); text-align: justify;
  }
  .about-text p + p { margin-top: 24px; }
</style>
</head>
<body>
<main class="bio-page">
  <div class="blue-band"></div>
  <div class="grey-panel"></div>
  <div class="photo-ring"></div>
  <div class="headshot" role="img" aria-label="Headshot photo of Daniel Rowe"></div>

  <h1 class="person-name"><span class="first">DANIEL</span> ROWE</h1>

  <div class="contact phone">
    <svg class="contact-icon" viewBox="0 0 41 41" aria-hidden="true">
      <circle cx="20.5" cy="20.5" r="20.5" fill="var(--icon-blue)"/>
      <path d="M14.5 12.5c1-.8 2-.6 2.5.3l1.6 2.8c.4.8.2 1.6-.5 2.1l-1 .8c.8 2 2.4 3.6 4.4 4.4l.8-1c.5-.7 1.3-.9 2.1-.5l2.8 1.6c.9.5 1.1 1.5.3 2.5l-1 1.2c-.9 1-2.3 1.3-3.6.8-4.4-1.6-7.8-5-9.4-9.4-.5-1.3-.2-2.7.8-3.6z" fill="#fff"/>
    </svg>
    <div class="contact-label">CALL US:</div>
    <div class="contact-value">+1 (555) 010 0142</div>
  </div>

  <div class="contact email">
    <svg class="contact-icon" viewBox="0 0 41 41" aria-hidden="true">
      <circle cx="20.5" cy="20.5" r="20.5" fill="var(--icon-blue)"/>
      <rect x="12" y="14" width="17" height="13" rx="1.5" fill="#fff"/>
      <path d="M12.5 15l8 6.2 8-6.2" fill="none" stroke="var(--icon-blue)" stroke-width="1.6"/>
    </svg>
    <div class="contact-label">EMAIL US:</div>
    <div class="contact-value">info@kvtgroup.com</div>
  </div>

  <div class="brand-name">KVT</div>

  <h2 class="about-title">ABOUT ME</h2>
  <section class="about-text">
    <p>Sed ut perspiciatis unde omnis iste natus error sit voluptatem accusantium doloremque laudantium, totam rem aperiam, eaque ipsa quae ab illo inventore veritatis et quasi architecto beatae vitae dicta sunt explicabo. Nemo enim ipsam voluptatem quia voluptas sit aspernatur aut odit aut fugit, sed quia consequuntur magni dolores eos qui ratione voluptatem sequi nesciunt. Neque porro quisquam est, qui dolorem ipsum quia dolor sit amet, consectetur, adipisci velit, sed quia non numquam eius modi tempora incidunt ut labore et dolore magnam aliquam quaerat voluptatem. Ut enim ad minima veniam, quis nostrum exercitationem ullam corporis suscipit laboriosam, nisi ut aliquid ex ea commodi consequa em vel eum iure reprehenderit qui in ea voluptate velit esse quam nihil.</p>
    <p>Veritatis et quasi architecto beatae vitae dicta sunt explicabo. Nemo enim ipsam voluptatem quia voluptas sit aspernatur aut odit aut fugit, sed quia consequuntur magni dolores eos qui ratione voluptatem sequi nesciunt. Neque porro quisquam est, qui dolorem ipsum quia dolor sit amet, consectetur, adipisci velit, sed quia non numquam eius modi tempora incidunt ut labore et dolore magnam aliquam quaerat voluptatem. Ut enim ad minima veniam, quis nostrum exercitationem ullam corporis suscipit laboriosam, nisi ut aliquid.</p>
    <p>Sed ut perspiciatis unde omnis iste natus error sit voluptatem accusantium doloremque laudantium, totam rem aperiam, eaque ipsa quae ab illo inventore veritatis et quasi architecto beatae vitae dicta sunt explicabo. Nemo enim ipsam voluptatem quia voluptas sit aspernatur aut odit aut fugit, sed quia consequuntur magni dolores eos qui ratione voluptatem sequi nesciunt. Neque porro quisquam est, qui dolorem ipsum quia dolor sit amet, consectetur, adipisci velit, sed quia non numquam eius modi tempora incidunt ut labore et dolore magnam aliquam quaerat voluptatem. Ut enim ad minima veniam, quis nostrum exercitationem ullam corporis suscipit laboriosam, nisi ut aliquid ex ea commodi consequa em vel eum iure reprehenderit qui in ea voluptate velit esse quam nihil.</p>
  </section>
</main>
</body>
</html>
```